Presentation Of Our Epidemiology Consulting Framework

We need a slide deck (png files) for PowerPoint that describes our organization and type of clients we serve, and our 6 phase framework that explains how we work with clients. Please use the minimum amount of text on each slide.  We want a more visual display of how to work with us. We want it to look very similar to our brochure.  We want to also have a few extra branded slides without text that can be used as a template if we decide to add to the deck later or create a new slide deck.
Colors
#56588C
#F28444
#F2E088
#F24C27
#ODODOD

```html
<!DOCTYPE html>
<html lang="en">
<head>
<meta charset="utf-8">
<title>Epidemiology Consulting Framework – Slide Deck</title>
<link href="https://fonts.googleapis.com/css2?family=Montserrat:wght@300;400;500;600&display=swap" rel="stylesheet">
<style>
  :root{
    --purple:#56588C;
    --orange:#F28444;
    --sun:#F2E088;
    --red:#F24C27;
    --ink:#0D0D0D;
    --navy:#0F0C25;
    --page:#F3F3F3;
    --white:#FFFFFF;
    --muted:#6A6A6A;
  }
  *{box-sizing:border-box;margin:0;padding:0}
  html,body{width:1045px;height:1200px;overflow:hidden;background:var(--page)}
  body{position:relative;font-family:'Montserrat',sans-serif;color:var(--ink)}

  .slide{position:absolute;width:478px;height:268px;background:var(--white);overflow:hidden}
  .col-a{left:22px}.col-b{left:518px}
  .row-1{top:22px}.row-2{top:313px}.row-3{top:602px}.row-4{top:896px}

  .slide-title{position:absolute;left:42px;top:11px;font-size:17px;font-weight:500;color:var(--orange);white-space:nowrap}
  .title-dot{position:absolute;left:11px;top:12px;width:22px;height:22px;border-radius:50%;background:var(--purple)}

  .footer{position:absolute;left:0;bottom:0;width:100%;height:39px;background:var(--navy);display:flex;align-items:center;justify-content:space-between;padding:0 10px 0 14px}
  .brand{display:flex;align-items:center;gap:7px;font-size:19px;font-weight:600;color:var(--orange);white-space:nowrap}
  .brand-dot{width:14px;height:14px;border-radius:50%;background:var(--orange)}
  .page-no{font-size:9.5px;font-weight:500;color:var(--white)}

  .subhead{position:absolute;font-size:14.5px;font-weight:500;line-height:1.38;color:var(--ink)}
  .bullets{position:absolute;list-style:none;font-size:9.5px;font-weight:500;line-height:15px;color:var(--ink)}
  .bullets.large{font-size:10.5px;line-height:20px}
  .bullets li{position:relative;padding-left:14px}
  .bullets li::before{content:"";position:absolute;left:0;top:4px;width:8px;height:8px;border-radius:50%;background:var(--ink)}
  .bullets li::after{content:"";position:absolute;left:2px;top:6.5px;width:2.5px;height:2.5px;border-top:1.2px solid var(--white);border-right:1.2px solid var(--white);transform:rotate(45deg)}
  .bullets.large li::before{top:6px}.bullets.large li::after{top:8.5px}

  .photo{position:absolute;border-radius:14px 14px 70px 14px}
  .photo-framed{border:3px solid var(--orange);border-radius:14px 14px 70px 14px}

  .icon-tile{position:absolute;width:51px;height:51px;background:var(--navy);border-radius:18px 6px 18px 6px;display:flex;align-items:center;justify-content:center}
  .icon-tile svg{width:30px;height:30px;fill:none;stroke:var(--white);stroke-width:1.4;stroke-linecap:round;stroke-linejoin:round}

  /* cover */
  .cover{background:linear-gradient(120deg,#2B2554 0%,#4B4688 55%,#6A64AE 100%)}
  .cover-brand{position:absolute;left:0;top:0;width:100%;height:100%;display:flex;align-items:center;justify-content:center;gap:12px;font-size:42px;font-weight:600;color:var(--orange)}
  .cover-brand .brand-dot{width:30px;height:30px}

  /* phase 3 */
  .center-head{position:absolute;left:0;width:100%;text-align:center}
  .step-label{position:absolute;width:110px;text-align:center;font-size:9px;line-height:13px;color:#4A4A4A}

  /* phase 4 quadrants */
  .petal{position:absolute;width:85px;height:85px}

  /* why partner */
  .reason{position:absolute;width:150px}
  .reason h3{font-size:8.5px;font-weight:500;color:var(--red);letter-spacing:.2px;margin-bottom:4px}
  .reason p{font-size:6px;line-height:10px;color:var(--muted)}
</style>
</head>
<body>

<!-- Cover -->
<section class="slide col-a row-1 cover" role="img" aria-label="Cover: group of smiling diverse people behind a purple overlay with the brand name">
  <div class="cover-brand"><span class="brand-dot"></span>Dr R Ellison</div>
</section>

<!-- Phase 1 -->
<section class="slide col-b row-1">
  <span class="title-dot"></span>
  <h2 class="slide-title">Phase 1: Discovery &amp; Vision Alignment</h2>
  <p class="subhead" style="left:47px;top:52px">Building the<br>Foundation for Success</p>
  <ul class="bullets" style="left:47px;top:104px;width:225px">
    <li>Deep-dive exploration of your organization's unique challenges and opportunities</li>
    <li>Strategic alignment of goals and expectations</li>
    <li>Custom-tailored solution design</li>
    <li>Clear roadmap development with defined milestones</li>
  </ul>
  <div class="photo" style="left:281px;top:42px;width:183px;height:168px;background:linear-gradient(135deg,#E9A15A,#C4553C 45%,#6E7FA0)" role="img" aria-label="Photo of a joyful diverse community group in colourful clothing"></div>
  <footer class="footer"><span class="brand"><span class="brand-dot"></span>Dr R Ellison</span><span class="page-no">Page No: 01</span></footer>
</section>

<!-- Phase 2 -->
<section class="slide col-a row-2">
  <span class="title-dot"></span>
  <h2 class="slide-title">Phase 2: Partnership Launch</h2>
  <div class="photo photo-framed" style="left:19px;top:43px;width:186px;height:170px;background:radial-gradient(circle at 45% 45%,#F28444 0%,#6A3A3A 25%,#1E3A5C 60%,#122238 100%)" role="img" aria-label="Illustration of a glowing rocket launching above an open hand in a sparkling night sky"></div>
  <p class="subhead" style="left:228px;top:52px">Setting the Stage for<br>Excellence</p>
  <ul class="bullets" style="left:228px;top:104px;width:240px">
    <li>Formation of dedicated project team</li>
    <li>Establishment of collaborative workflow</li>
    <li>Comprehensive data gathering</li>
    <li>Strategic timeline planning</li>
    <li>Stakeholder engagement and vision capture</li>
  </ul>
  <footer class="footer"><span class="brand"><span class="brand-dot"></span>Dr R Ellison</span><span class="page-no">Page No: 03</span></footer>
</section>

<!-- Phase 3 -->
<section class="slide col-b row-2">
  <span class="title-dot"></span>
  <h2 class="slide-title">Phase 3: Expert Execution</h2>
  <p class="center-head" style="top:44px;font-size:14px;font-weight:500">Where Science Meets Service</p>
  <p class="center-head" style="top:65px;font-size:9.5px;font-weight:300;color:#555">Our specialized team begins the transformation process</p>

  <div class="icon-tile" style="left:35px;top:101px"><svg viewBox="0 0 30 30"><path d="M5 25h20M7 25v-6M11 25v-9M15 25v-7M19 25v-11M23 25v-14M6 15l5-5 4 3 8-8M20 5h3v3"/></svg></div>
  <div class="icon-tile" style="left:154px;top:101px"><svg viewBox="0 0 30 30"><circle cx="15" cy="10" r="5"/><path d="M6 26v-4a9 9 0 0 1 18 0v4M11 20h8v5h-8z"/></svg></div>
  <div class="icon-tile" style="left:273px;top:101px"><svg viewBox="0 0 30 30"><path d="M4 4h6v8H4zM12 4h6v8h-6zM20 4h6v8h-6zM15 14v6M12 17l3 3 3-3M6 22h18v4H6z"/></svg></div>
  <div class="icon-tile" style="left:392px;top:101px"><svg viewBox="0 0 30 30"><circle cx="15" cy="15" r="9"/><path d="M6 15h18M15 6c-4 5-4 13 0 18M15 6c4 5 4 13 0 18M7 7l16 16"/></svg></div>

  <p class="step-label" style="left:5px;top:166px">In-depth research<br>and analysis</p>
  <p class="step-label" style="left:124px;top:166px">Content development<br>and refinement</p>
  <p class="step-label" style="left:243px;top:166px">Data interpretation<br>and visualization</p>
  <p class="step-label" style="left:357px;top:166px;width:120px">Plain language translation of complex health information</p>
  <footer class="footer"><span class="brand"><span class="brand-dot"></span>Dr R Ellison</span><span class="page-no">Page No: 04</span></footer>
</section>

<!-- Phase 4 -->
<section class="slide col-a row-3">
  <span class="title-dot"></span>
  <h2 class="slide-title">Phase 4: Collaborative Refinement</h2>
  <p class="subhead" style="left:46px;top:56px">Ensuring Perfect<br>Alignment</p>
  <ul class="bullets" style="left:46px;top:110px;width:230px">
    <li>Formation of dedicated project team</li>
    <li>Establishment of collaborative workflow</li>
    <li>Comprehensive data gathering</li>
    <li>Strategic timeline planning</li>
    <li>Stakeholder engagement and vision capture</li>
  </ul>
  <div role="img" aria-label="Four-part artwork of small figures walking toward a glowing light bulb on crumpled teal and orange paper">
    <div class="petal" style="left:282px;top:40px;border-radius:85px 6px 85px 6px;background:linear-gradient(135deg,#2F7E7A,#6CB2A2)"></div>
    <div class="petal" style="left:373px;top:40px;border-radius:6px 85px 6px 85px;background:linear-gradient(135deg,#F2E088,#F28444)"></div>
    <div class="petal" style="left:282px;top:131px;border-radius:6px 85px 6px 85px;background:linear-gradient(135deg,#1F5E63,#3E9089)"></div>
    <div class="petal" style="left:373px;top:131px;border-radius:85px 6px 85px 6px;background:linear-gradient(135deg,#F28444,#1F4F5C)"></div>
  </div>
  <footer class="footer"><span class="brand"><span class="brand-dot"></span>Dr R Ellison</span><span class="page-no">Page No: 05</span></footer>
</section>

<!-- Phase 5 -->
<section class="slide col-b row-3">
  <span class="title-dot"></span>
  <h2 class="slide-title">Phase 5: Impact Delivery</h2>
  <div class="photo" style="left:34px;top:48px;width:183px;height:168px;border-radius:14px 6px 70px 6px;background:linear-gradient(90deg,#3A5B72 0%,#F2C83C 45%,#E94B3C 85%,#3A5B72 100%)" role="img" aria-label="Photo of colourful paper-cut people holding hands on a blue wooden table"></div>
  <p class="subhead" style="left:238px;top:60px">Bringing Vision to Reality</p>
  <ul class="bullets large" style="left:238px;top:98px;width:230px">
    <li>Final deliverable presentation</li>
    <li>Implementation support</li>
    <li>Knowledge transfer</li>
    <li>Impact measurement framework</li>
  </ul>
  <footer class="footer"><span class="brand"><span class="brand-dot"></span>Dr R Ellison</span><span class="page-no">Page No: 06</span></footer>
</section>

<!-- Phase 6 -->
<section class="slide col-a row-4">
  <span class="title-dot"></span>
  <h2 class="slide-title">Phase 6: Evolution &amp; Growth</h2>
  <p class="subhead" style="left:44px;top:48px">Sustaining Long-term<br>Success</p>
  <ul class="bullets large" style="left:44px;top:100px;width:200px">
    <li>Project success celebration</li>
    <li>Future opportunities exploration</li>
    <li>Partnership evolution planning</li>
    <li>Continuous improvement recommendations</li>
  </ul>
  <div class="photo" style="left:254px;top:45px;width:186px;height:172px;border-radius:70px 10px 70px 6px;border-top:3px solid var(--orange);border-right:3px solid var(--orange);background:radial-gradient(circle at 40% 35%,#D9D36A 0%,#6C8A2E 40%,#2E3A1A 75%,#3A2A1C 100%)" role="img" aria-label="Photo of young green seedlings sprouting from dark soil in warm light"></div>
  <footer class="footer"><span class="brand"><span class="brand-dot"></span>Dr R Ellison</span><span class="page-no">Page No: 07</span></footer>
</section>

<!-- Why partner -->
<section class="slide col-b row-4">
  <span class="title-dot"></span>
  <h2 class="slide-title">Why Partner With Us?</h2>

  <div class="icon-tile" style="left:34px;top:60px"><svg viewBox="0 0 30 30"><path d="M5 25h20M7 25v-6M11 25v-9M15 25v-7M19 25v-11M23 25v-14M6 15l5-5 4 3 8-8M20 5h3v3"/></svg></div>
  <div class="reason" style="left:95px;top:64px"><h3>EXPERTISE</h3><p>Our diverse team of innovative global public health professionals, specialized in epidemiology and health communication</p></div>

  <div class="icon-tile" style="left:254px;top:60px"><svg viewBox="0 0 30 30"><path d="M15 5a7 7 0 0 0-4 12.7V21h8v-3.3A7 7 0 0 0 15 5zM12 24h6M13 27h4M4 12h2M24 12h2M7 5l1.5 1.5M23 5l-1.5 1.5"/></svg></div>
  <div class="reason" style="left:315px;top:64px"><h3>INNOVATION</h3><p>Custom solutions tailored to BIPOC community needs</p></div>

  <div class="icon-tile" style="left:34px;top:137px"><svg viewBox="0 0 30 30"><circle cx="15" cy="15" r="4"/><circle cx="7" cy="7" r="3"/><circle cx="23" cy="7" r="3"/><circle cx="7" cy="23" r="3"/><circle cx="23" cy="23" r="3"/><path d="M9 9l3 3M21 9l-3 3M9 21l3-3M21 21l-3-3"/></svg></div>
  <div class="reason" style="left:95px;top:141px"><h3>IMPACT</h3><p>Proven track record of transforming complex health data into accessible information</p></div>

  <div class="icon-tile" style="left:254px;top:137px"><svg viewBox="0 0 30 30"><path d="M3 12l6-5 5 3 4-3 9 5M3 12l8 9 3-2 3 2 2-2 3 1 5-8M11 14l4 4M14 12l4 4"/></svg></div>
  <div class="reason" style="left:315px;top:141px"><h3>PARTNERSHIP</h3><p>Collaborative approach ensuring lasting results</p></div>

  <footer class="footer"><span class="brand"><span class="brand-dot"></span>Dr R Ellison</span><span class="page-no">Page No: 08</span></footer>
</section>

</body>
</html>
```